Redesign of the UI of a customer service platform

To improve the user experience of our customers, we need a new design for our agent interface of our customer service platform (velorant.com).
The focus will be on the dashboard and the inbox screens (see attached) along with the common UI elements (Buttons, menu, fonts, forms...)
We want a simple and distinctive design

Target Market(s)

Worldwide

Industry/Entity Type

It Service

Number of Pages Required

3 page

Font styles to use
Sans Serif

Requirements
Must have
• New Onboarding page: this is a new page that is shown to user the first time they login to the platform. This will replace the current onboarding screen (setup SMS, Setup widget...etc)
• Dashboard page: to access important information and activate services (see screenshot from current site)
• Inbox page: to manage all the interactions with customers. (see screenshot from current site)
• UI elements (buttons, menus, forms, tables, fonts, color palette)

```html
<!DOCTYPE html>
<html lang="en">
<head>
<meta charset="utf-8">
<title>Velorant – Inbox</title>
<link href="https://fonts.googleapis.com/css2?family=Open+Sans:wght@400;600&display=swap" rel="stylesheet">
<style>
:root{
  --ink:#444;--muted:#777;--line:#e3e3e3;--panel:#f5f5f5;--band:#f1f1f1;
  --blue:#3a94c0;--accent:#2f8fc4;--red:#e74c3c;--coral:#ee7a72;--sky:#5fd0ea;
  --teal:#3ed8c3;--azure:#5cbdee;--green:#27ae60;--badge:#2ecc8f;
  --bubble:#dcfbfd;--bubble-line:#b6eff2;--ring:#a4ecef;--photo-a:#c9a08a;--photo-b:#6b4a3c;
}
*{box-sizing:border-box;margin:0;padding:0}
html,body{width:1155px;height:1200px;overflow:hidden;background:#fff;font-family:"Open Sans",sans-serif;color:var(--ink);font-size:12px}
.abs{position:absolute}
.photo{border-radius:50%;background:radial-gradient(circle at 50% 40%,var(--photo-a),var(--photo-b));}
/* top bar */
.topbar{position:absolute;left:0;top:0;width:1155px;height:59px;border-bottom:1px solid var(--line);background:#fff}
.brand{left:0;top:0;width:82px;height:59px;display:flex;align-items:center;justify-content:center}
.brand span{width:40px;height:40px;border-radius:50%;background:#333}
.tab{top:0;width:96px;height:59px;border-left:1px solid var(--line);text-align:center;font-size:10px;color:#555;padding-top:36px}
.tab svg{position:absolute;left:41px;top:14px}
.tab.active{background:#f3f3f3}
.count{position:absolute;top:24px;left:68px;width:22px;height:22px;border-radius:50%;color:#fff;font-size:11px;line-height:22px}
.user{left:1005px;top:8px;display:flex;align-items:center;gap:8px;font-size:10.5px;color:#555}
.user .photo{width:44px;height:44px;border:2px solid var(--ring);position:relative}
.online{position:absolute;left:-2px;top:2px;width:10px;height:10px;border-radius:50%;background:var(--badge)}
/* conversation list */
.list{left:0;top:59px;width:331px;height:1089px;background:var(--panel);border-right:1px solid var(--line)}
.list-head{height:71px;background:var(--blue);color:#fff;text-align:center;padding-top:14px;position:relative}
.list-head h2{font-size:16.5px;font-weight:400}
.list-head p{font-size:12px;margin-top:1px}
.list-head svg{position:absolute;right:24px;top:31px}
.conv{position:relative;height:68px;background:#fff;border-bottom:1px solid var(--line)}
.conv .photo{position:absolute;left:16px;top:11px;width:46px;height:46px;border:2px solid #ddd}
.conv .name{position:absolute;left:72px;top:15px;font-size:13.5px;color:#333}
.conv .snip{position:absolute;left:72px;top:40px;font-size:10.5px;color:#888;display:flex;align-items:center;gap:4px;white-space:nowrap}
.conv .time{position:absolute;right:15px;top:12px;font-size:9.5px;color:var(--red)}
.mini{position:absolute;top:28px;width:22px;height:22px;border:1.5px solid #ddd}
.dot{width:7px;height:7px;border-radius:50%;background:var(--azure)}
/* profile */
.profile{left:331px;top:59px;width:421px;height:1089px;border-right:1px solid var(--line)}
.btn{position:absolute;height:26px;color:#fff;font-size:12px;display:flex;align-items:center;justify-content:center;gap:5px;border-radius:2px;white-space:nowrap}
.big-photo{left:104px;top:72px;width:186px;height:186px;border:8px solid #eee}
.pname{left:0;width:476px;text-align:center;top:270px;font-size:17px;color:var(--accent)}
.meta{left:304px;font-size:12px;display:flex;gap:6px;align-items:center;color:#555}
.band{position:absolute;left:0;width:421px;height:39px;background:linear-gradient(#fafafa,var(--band));border-top:1px solid var(--line);border-bottom:1px solid var(--line);font-size:12.5px;color:#555;padding:12px 17px;display:flex;justify-content:space-between}
.row{position:absolute;left:0;width:421px;font-size:12px;white-space:nowrap}
.row .k{position:absolute;right:296px;color:#555}
.row .v{position:absolute;left:146px;color:#555}
.row svg{position:absolute;left:378px;top:1px}
.task{position:absolute;left:16px;font-size:10.5px;color:#555;width:390px;white-space:nowrap}
.task .d{position:absolute;left:242px}
.card{position:absolute;top:973px;width:116px;height:99px;border-radius:5px;color:#fff;text-align:center;font-size:12.5px;line-height:19px;padding-top:57px}
.card svg{position:absolute;left:44px;top:17px}
.card .q{position:absolute;left:71px;top:10px;background:#2c8ad8;font-size:10px;line-height:16px;padding:0 6px;border-radius:2px}
/* chat */
.chat{left:752px;top:59px;width:403px;height:1112px}
.msg{position:absolute;background:var(--bubble);border:1px solid var(--bubble-line);font-size:11.5px;color:#555;padding:9px 0 9px 17px;line-height:22px;white-space:nowrap}
.msg.long{height:62px;padding-left:20px}
.msg.short{height:42px;padding-top:9px}
.msg.agent{height:42px;padding-left:11px}
.av{position:absolute;width:66px;height:66px;border:3px solid var(--ring)}
.composer{left:25px;top:1020px;width:350px;height:56px;background:var(--bubble);border:1px solid var(--bubble-line);padding:8px}
.composer div{background:#fff;border:1px solid var(--bubble-line);height:40px;padding:11px 14px;font-size:12px;color:#555}
.footer{left:0;top:1171px;width:1155px;height:29px;background:var(--band);border-top:1px solid var(--line);text-align:center;font-size:9.5px;line-height:28px;color:#555}
</style>
</head>
<body>

<header class="topbar">
  <div class="abs brand"><span role="img" aria-label="Support agent emblem"></span></div>
  <div class="abs tab active" style="left:82px"><svg width="14" height="12" viewBox="0 0 14 12"><rect x="1" y="1" width="12" height="10" fill="none" stroke="#777"/><path d="M1 1l6 5 6-5" fill="none" stroke="#777"/></svg>INBOX<span class="count" style="background:var(--badge)">4</span></div>
  <div class="abs tab" style="left:178px"><svg width="12" height="14" viewBox="0 0 12 14"><path d="M1 1h7l3 3v9H1z" fill="none" stroke="#777"/><path d="M3 7h6M3 10h6" stroke="#777"/></svg>TASKS<span class="count" style="background:var(--azure)">4</span></div>
  <div class="abs tab" style="left:274px"><svg width="12" height="14" viewBox="0 0 12 14"><circle cx="6" cy="4" r="3" fill="#777"/><path d="M1 13c0-4 2-6 5-6s5 2 5 6z" fill="#777"/></svg>CUSTOMERS</div>
  <div class="abs tab" style="left:370px"><svg width="14" height="14" viewBox="0 0 14 14"><path d="M1 7l12-6-3 12-3-4z" fill="none" stroke="#777"/></svg>CAMPAIGNS</div>
  <div class="abs tab" style="left:466px"><svg width="14" height="12" viewBox="0 0 14 12"><rect x="1" y="1" width="12" height="10" fill="none" stroke="#777"/><path d="M1 4h12" stroke="#777" stroke-width="2"/></svg>PAYMENTS</div>
  <div class="abs tab" style="left:562px"><svg width="14" height="12" viewBox="0 0 14 12"><path d="M1 11h12M3 10V5M6 10V2M9 10V6M12 10V4" stroke="#777"/></svg>REPORTS</div>
  <div class="abs tab" style="left:658px;border-right:1px solid var(--line)"><svg width="13" height="13" viewBox="0 0 13 13"><circle cx="6.5" cy="6.5" r="4.5" fill="none" stroke="#777" stroke-width="3" stroke-dasharray="2 1.5"/></svg>SETTINGS</div>
  <div class="abs user"><div class="photo" role="img" aria-label="Agent profile photo"><span class="online"></span></div>MARCO BELLINI</div>
</header>

<aside class="abs list">
  <div class="list-head"><h2>Open Conversations</h2><p>New or assigned to me</p>
    <svg width="12" height="8" viewBox="0 0 12 8"><path d="M1 1l5 5 5-5" fill="none" stroke="#fff" stroke-width="1.5"/></svg></div>
  <div class="conv"><div class="photo" role="img" aria-label="Customer photo"></div><div class="name">Lena Moravec</div>
    <div class="snip"><svg width="13" height="12" viewBox="0 0 14 14"><path d="M1 7l12-6-3 12-3-4z" fill="none" stroke="#5cbdee" stroke-width="1.4"/></svg>Yes that would be great, please</div>
    <div class="time">2 mins ago</div><div class="mini photo" style="right:15px" role="img" aria-label="Assigned agent photo"></div></div>
  <div class="conv"><div class="photo" role="img" aria-label="Customer photo"></div><div class="name">Owen Hartley</div>
    <div class="snip"><svg width="14" height="12" viewBox="0 0 14 12"><rect x="1" y="1" width="12" height="7" fill="none" stroke="#5cbdee" stroke-width="1.5"/><path d="M4 11h6" stroke="#5cbdee" stroke-width="1.5"/></svg>Hi, I need to know if there are...</div>
    <div class="time">9 mins ago</div></div>
  <div class="conv"><div class="photo" role="img" aria-label="Customer photo"></div><div class="name">Lena Moravec</div>
    <div class="snip"><span class="dot"></span>The issue occured one more...</div>
    <div class="time">2 mins ago</div><div class="mini photo" style="right:43px" role="img" aria-label="Agent photo"></div><div class="mini photo" style="right:15px" role="img" aria-label="Agent photo"></div></div>
  <div class="conv"><div class="photo" role="img" aria-label="Customer photo"></div><div class="name">Owen Hartley</div>
    <div class="snip"><svg width="14" height="12" viewBox="0 0 14 12"><rect x="1" y="1" width="12" height="7" fill="none" stroke="#5cbdee" stroke-width="1.5"/><path d="M4 11h6" stroke="#5cbdee" stroke-width="1.5"/></svg>Hi, I need to know if there are...</div>
    <div class="time">9 mins ago</div></div>
</aside>

<main class="abs profile">
  <div class="btn" style="left:204px;top:19px;width:75px;background:var(--sky);border:1px solid #3fbfe0"><svg width="10" height="8" viewBox="0 0 10 8"><path d="M1 4l3 3 5-6" fill="none" stroke="#fff" stroke-width="1.8"/></svg>Close</div>
  <div class="btn" style="left:287px;top:19px;width:74px;background:var(--coral);border:1px solid #e0625a"><svg width="11" height="9" viewBox="0 0 11 9"><path d="M1 8c1-4 4-5 6-5V1l3 3-3 3V5C5 5 3 6 1 8z" fill="#fff"/></svg>Transfer</div>
  <svg class="abs" style="left:375px;top:25px" width="4" height="16" viewBox="0 0 4 16"><circle cx="2" cy="2" r="1.6" fill="#555"/><circle cx="2" cy="8" r="1.6" fill="#555"/><circle cx="2" cy="14" r="1.6" fill="#555"/></svg>
  <div class="abs photo big-photo" role="img" aria-label="Customer portrait"></div>
  <div class="abs pname">Lena Moravec</div>
  <div class="abs meta" style="top:148px"><svg width="13" height="12" viewBox="0 0 14 14"><path d="M1 7l12-6-3 12-3-4z" fill="none" stroke="#2ecc71" stroke-width="1.6"/></svg>Chatline</div>
  <div class="abs meta" style="top:174px"><svg width="13" height="13" viewBox="0 0 10 13"><path d="M5 12S1 7 1 4.5a4 4 0 018 0C9 7 5 12 5 12z" fill="#2ecc71"/><circle cx="5" cy="4.5" r="1.5" fill="#fff"/></svg>United States</div>

  <div class="band" style="top:330px"><span>Details</span><span>+ Add</span></div>
  <div class="row" style="top:396px"><span class="k">ID :</span><span class="v">41</span></div>
  <div class="row" style="top:422px"><span class="k">Email :</span><span class="v">lena.moravec@mailbox.test</span><svg width="13" height="13" viewBox="0 0 13 13"><path d="M2 11l1-3 6-6 2 2-6 6z" fill="#5cbdee"/></svg></div>
  <div class="row" style="top:448px"><span class="k">Phone :</span><span class="v">+1 (555) 014 2291</span><svg width="13" height="13" viewBox="0 0 13 13"><path d="M2 11l1-3 6-6 2 2-6 6z" fill="#5cbdee"/></svg></div>
  <div class="row" style="top:474px"><span class="k">Address Line 1 :</span><span class="v">48 Alder Brook Road</span><svg width="13" height="13" viewBox="0 0 13 13"><path d="M2 11l1-3 6-6 2 2-6 6z" fill="#5cbdee"/></svg></div>
  <div class="row" style="top:500px"><span class="k">City :</span><span class="v">Millbrook</span><svg width="13" height="13" viewBox="0 0 13 13"><path d="M2 11l1-3 6-6 2 2-6 6z" fill="#5cbdee"/></svg></div>
  <div class="row" style="top:526px"><span class="k">State :</span><span class="v">North Carolina</span><svg width="13" height="13" viewBox="0 0 13 13"><path d="M2 11l1-3 6-6 2 2-6 6z" fill="#5cbdee"/></svg></div>
  <div class="btn" style="left:169px;top:568px;width:84px;height:25px;background:var(--coral);border:1px solid #e0625a"><svg width="9" height="6" viewBox="0 0 9 6"><path d="M1 1l3.5 3.5L8 1" fill="none" stroke="#fff" stroke-width="1.4"/></svg>Show All</div>

  <div class="band" style="top:627px"><span>Tasks</span><span>+ Add</span></div>
  <div class="task" style="top:693px"><svg width="11" height="9" viewBox="0 0 10 8" style="vertical-align:-1px;margin-right:8px"><path d="M1 4l3 3 5-6" fill="none" stroke="#2ecc71" stroke-width="2"/></svg>Verify customer identity<span class="d">2017-15-01</span>
    <svg class="abs" style="left:374px;top:0" width="10" height="12" viewBox="0 0 10 12"><path d="M1 2h8M3 2V1h4v1M2 3h6l-1 8H3z" fill="#5cbdee" stroke="#5cbdee"/></svg></div>
  <div class="task" style="top:719px"><svg width="11" height="11" viewBox="0 0 11 11" style="vertical-align:-1px;margin-right:8px"><circle cx="5.5" cy="5.5" r="4.5" fill="none" stroke="#2ecc71" stroke-width="1.5"/><path d="M5.5 3v3h2" fill="none" stroke="#2ecc71" stroke-width="1.3"/></svg>Check if the customer was billed twice<span class="d">2017-16-01</span>
    <svg class="abs" style="left:338px;top:1px" width="11" height="9" viewBox="0 0 10 8"><path d="M1 4l3 3 5-6" fill="none" stroke="#5cbdee" stroke-width="2"/></svg>
    <svg class="abs" style="left:357px;top:1px" width="9" height="9" viewBox="0 0 9 9"><path d="M1 1l7 7M8 1L1 8" stroke="#5cbdee" stroke-width="2"/></svg>
    <svg class="abs" style="left:374px;top:-1px" width="10" height="12" viewBox="0 0 10 12"><path d="M1 2h8M3 2V1h4v1M2 3h6l-1 8H3z" fill="#5cbdee" stroke="#5cbdee"/></svg></div>

  <div class="band" style="top:775px"><span>Notes</span><span>+ Add</span></div>
  <div class="row" style="top:834px;text-align:center;font-size:13px;color:#555;padding-left:22px">Empty</div>

  <div class="band" style="top:870px"><span>Plan</span><span></span></div>
  <div class="row" style="top:929px;left:17px;font-size:13px;color:#555">Plan (Pro)</div>
  <div class="btn" style="left:331px;top:928px;width:79px;height:23px;background:var(--green);font-size:11px"><svg width="10" height="8" viewBox="0 0 10 8"><path d="M1 4l3 3 5-6" fill="none" stroke="#fff" stroke-width="1.8"/></svg>Upgrade</div>

  <div class="card" style="left:16px;background:var(--coral);border:1px solid #e0625a"><svg width="28" height="24" viewBox="0 0 28 24"><circle cx="14" cy="6" r="4.5" fill="#fff"/><circle cx="5" cy="9" r="3.5" fill="#fff"/><circle cx="23" cy="9" r="3.5" fill="#fff"/><path d="M6 24c0-7 4-11 8-11s8 4 8 11zM0 20c0-5 2-7 5-7s4 2 4 2l-3 5zM28 20c0-5-2-7-5-7s-4 2-4 2l3 5z" fill="#fff"/></svg><span class="q">1/1</span>Agents<br>Unlimited</div>
  <div class="card" style="left:153px;background:var(--teal)"><svg width="28" height="24" viewBox="0 0 28 24"><path d="M10 5V2h8v3" fill="none" stroke="#fff" stroke-width="2"/><rect x="1" y="5" width="26" height="18" rx="2" fill="#fff"/><path d="M7 5v18M21 5v18" stroke="#3ed8c3" stroke-width="1.5"/></svg><span class="q">1/1</span>Departments<br>Unlimited</div>
  <div class="card" style="left:289px;background:var(--azure)"><svg width="24" height="24" viewBox="0 0 24 24"><path d="M5 2l4 5-2 3c1 3 4 6 7 7l3-2 5 4-3 4C10 22 2 14 1 5z" fill="#fff"/></svg><span class="q">1/1</span>Phone<br>Unlimited</div>
</main>

<section class="abs chat">
  <svg class="abs" style="left:377px;top:22px" width="4" height="16" viewBox="0 0 4 16"><circle cx="2" cy="2" r="1.6" fill="#555"/><circle cx="2" cy="8" r="1.6" fill="#555"/><circle cx="2" cy="14" r="1.6" fill="#555"/></svg>

  <div class="av photo" style="left:28px;top:30px" role="img" aria-label="Customer photo"></div>
  <div class="msg short" style="left:108px;top:42px;width:87px">Hello</div>
  <div class="msg long" style="left:107px;top:93px;width:229px">Lorem Ipsum is simply dummy text<br>of the printing</div>
  <div class="msg agent" style="left:107px;top:174px;width:188px">Lorem Ipsum is simply dummy</div>
  <div class="av photo" style="left:308px;top:162px" role="img" aria-label="Agent photo"></div>

  <div class="av photo" style="left:28px;top:228px" role="img" aria-label="Customer photo"></div>
  <div class="msg short" style="left:108px;top:240px;width:227px">Lorem Ipsum is simply</div>
  <div class="msg long" style="left:107px;top:291px;width:229px">Lorem Ipsum is simply dummy text<br>of the printing</div>
  <div class="msg agent" style="left:107px;top:372px;width:188px">Lorem Ipsum is simply dummy</div>
  <div class="av photo" style="left:308px;top:360px" role="img" aria-label="Agent photo"></div>

  <div class="av photo" style="left:28px;top:434px" role="img" aria-label="Customer photo"></div>
  <div class="msg short" style="left:108px;top:446px;width:227px">Lorem Ipsum is simply</div>
  <div class="msg long" style="left:107px;top:497px;width:229px">Lorem Ipsum is simply dummy text<br>of the printing</div>
  <div class="msg agent" style="left:107px;top:578px;width:188px">Lorem Ipsum is simply dummy</div>
  <div class="av photo" style="left:308px;top:566px" role="img" aria-label="Agent photo"></div>

  <div class="av photo" style="left:28px;top:641px" role="img" aria-label="Customer photo"></div>
  <div class="msg short" style="left:109px;top:653px;width:227px">Lorem Ipsum is simply</div>
  <div class="msg long" style="left:108px;top:704px;width:229px">Lorem Ipsum is simply dummy text<br>of the printing</div>
  <div class="msg agent" style="left:108px;top:785px;width:188px">Lorem Ipsum is simply dummy</div>
  <div class="av photo" style="left:309px;top:773px" role="img" aria-label="Agent photo"></div>

  <svg class="abs" style="left:268px;top:983px" width="12" height="18" viewBox="0 0 12 18"><path d="M10 4C9 3 8 2.5 6 2.5S2 3.5 2 5.5s2 2.5 4 3 4 1 4 3-2 3-4 3-3.5-.5-4.5-1.5M6 0v18" fill="none" stroke="#999" stroke-width="1.4"/></svg>
  <svg class="abs" style="left:296px;top:984px" width="16" height="17" viewBox="0 0 16 17"><path d="M13 8l-6 6a3 3 0 01-5-5l7-7a2 2 0 013 3l-7 7a1 1 0 01-1.5-1.5L9 5" fill="none" stroke="#999" stroke-width="1.4"/></svg>
  <svg class="abs" style="left:322px;top:985px" width="20" height="15" viewBox="0 0 20 15"><rect x="1" y="1" width="18" height="13" fill="none" stroke="#999" stroke-width="1.4"/><path d="M3 12l5-5 3 3 2-2 4 4z" fill="#999"/><circle cx="14" cy="5" r="1.5" fill="#999"/></svg>
  <svg class="abs" style="left:354px;top:984px" width="17" height="17" viewBox="0 0 17 17"><circle cx="8.5" cy="8.5" r="7.5" fill="none" stroke="#999" stroke-width="1.4"/><circle cx="6" cy="7" r="1" fill="#999"/><circle cx="11" cy="7" r="1" fill="#999"/><path d="M5 10.5c1 1.5 2 2 3.5 2s2.5-.5 3.5-2" fill="none" stroke="#999" stroke-width="1.3"/></svg>
  <div class="abs composer"><div>Your Message...</div></div>
</section>

<footer class="abs footer">Copyrights 2017. Velorant. All rights reserved.</footer>
</body>
</html>
```